Promotional brochure for educational consulting firm

Updates

Hi Designers!

Please do a 8.5 x 11 inch tri-fold brochure as well as a 8.5 x 11 inch half-fold brochure.  I appreciate black and white versions in addition to color.  Please take a look at my company's website for a better sense of the look and feel I am going for:  www.brightlanepa.org

Thanks!

Industry/Entity Type

Consulting

Colors
3176b5
85abd2
fcfbfd

```html
<!DOCTYPE html>
<html lang="en">
<head>
<meta charset="utf-8">
<title>Brightlane Associates LLC – Tri-fold Brochure</title>
<link href="https://fonts.googleapis.com/css2?family=Mulish:wght@400;600;700;800;900&display=swap" rel="stylesheet">
<style>
  :root {
    --brand-blue: #3176b5;
    --brand-blue-deep: #1a4f9c;
    --brand-blue-soft: #85abd2;
    --paper: #fcfbfd;
    --paper-shade: #ececef;
    --ink: #1f1f22;
    --ink-muted: #8a8a90;
    --backdrop: #d9d9dc;
  }
  * { box-sizing: border-box; margin: 0; padding: 0; }
  html, body {
    width: 1200px; height: 945px; overflow: hidden;
    background: var(--backdrop);
    font-family: "Mulish", sans-serif;
  }
  .brochure {
    position: absolute; left: 20px; top: 20px;
    width: 1160px; height: 905px;
    display: flex;
    box-shadow: 0 2px 6px rgba(0,0,0,.25);
  }
  .panel { position: relative; width: calc(100% / 3); height: 100%; }
  .panel--light { background: radial-gradient(ellipse at 50% 45%, var(--paper) 40%, var(--paper-shade) 100%); }
  .panel--blue { background: var(--brand-blue); overflow: hidden; }

  .photo { position: absolute; left: 0; right: 0; }
  .photo--pencils {
    top: 64px; height: 290px;
    background: linear-gradient(155deg, #1b1b1b 0%, #8a4a2c 22%, #d8344a 42%, #2f5fbf 62%, #e8679c 80%, #f0d64a 100%);
  }
  .photo--children {
    top: 290px; height: 282px;
    background: linear-gradient(180deg, var(--paper) 0%, #f4e2d4 40%, #e8a37a 62%, #e9d75a 78%, #7fc4e6 100%);
    border-bottom: 6px solid var(--brand-blue-soft);
  }

  .contact { position: absolute; top: 405px; left: 0; right: 0; text-align: center; }
  .contact__heading { color: var(--brand-blue-soft); font-weight: 700; font-size: 16px; letter-spacing: .3px; }
  .contact__name { margin-top: 44px; color: var(--brand-blue-deep); font-size: 19px; font-weight: 400; }
  .contact__line { display: flex; align-items: center; justify-content: center; gap: 5px; color: var(--ink); }
  .contact__line--phone { margin-top: 30px; font-size: 16px; font-weight: 800; }
  .contact__line--fax { margin-top: 16px; font-size: 14px; }
  .contact__line--email { margin-top: 28px; font-size: 14px; }
  .contact__line--web { margin-top: 14px; font-size: 14px; }
  .icon { width: 14px; height: 14px; flex: none; }

  .brand { position: absolute; left: 0; right: 0; text-align: center; }
  .brand__dot { display: block; margin: 0 auto; border-radius: 50%; }
  .brand__name { font-weight: 800; font-size: 19px; letter-spacing: .5px; text-transform: uppercase; }
  .brand__tagline { font-size: 11.5px; text-transform: uppercase; letter-spacing: .3px; }
  .brand--footer { top: 755px; }
  .brand--footer .brand__dot { width: 70px; height: 70px; background: var(--ink); margin-bottom: 14px; }
  .brand--footer .brand__name { color: var(--ink); }
  .brand--footer .brand__tagline { color: var(--ink); }
  .brand--masthead { top: 62px; }
  .brand--masthead .brand__dot { width: 96px; height: 96px; background: var(--brand-blue-deep); margin-bottom: 16px; }
  .brand--masthead .brand__name { color: var(--brand-blue-deep); }
  .brand--masthead .brand__tagline { color: var(--brand-blue-deep); }

  .backdrop-disc {
    position: absolute; left: 18px; top: 274px; width: 350px; height: 350px;
    border-radius: 50%; background: var(--brand-blue-deep); opacity: .35;
  }
  .headline { position: absolute; left: 0; right: 0; top: 420px; text-align: center; color: var(--paper); }
  .headline__lead { font-size: 29px; font-weight: 400; }
  .headline__figure { margin-top: 6px; font-size: 58px; font-weight: 900; letter-spacing: 1px; line-height: 1; }

  .pitch {
    position: absolute; left: 30px; right: 30px; top: 615px; text-align: center;
    color: var(--brand-blue); font-size: 22px; line-height: 1.27; font-weight: 400;
  }
  .callout { position: absolute; left: 0; right: 0; top: 818px; text-align: center; color: var(--ink-muted); }
  .callout__phone { display: flex; align-items: center; justify-content: center; gap: 5px; font-size: 21px; font-weight: 800; }
  .callout__phone .icon { width: 20px; height: 20px; }
  .callout__web { display: flex; align-items: center; justify-content: center; gap: 4px; font-size: 13px; margin-top: 2px; }
</style>
</head>
<body>
<main class="brochure">

  <section class="panel panel--light panel--contact">
    <div class="photo photo--pencils" role="img" aria-label="Close-up photo of sharpened coloured pencils"></div>
    <div class="contact">
      <h2 class="contact__heading">CONTACT US</h2>
      <p class="contact__name">Dana Marlow, Ed.D.</p>
      <p class="contact__line contact__line--phone">
        <svg class="icon" viewBox="0 0 16 16"><circle cx="8" cy="8" r="7" fill="none" stroke="var(--brand-blue-soft)" stroke-width="1.3"/><path d="M5.5 4.5c-.8 2.5.8 6 4 7l1-1.5-1.6-1-1 .8c-.8-.6-1.5-1.6-1.7-2.6l1-.6-.6-1.8z" fill="var(--brand-blue-soft)"/></svg>
        555.014.2290
      </p>
      <p class="contact__line contact__line--fax">
        <svg class="icon" viewBox="0 0 16 16"><rect x="2" y="8" width="12" height="6" fill="none" stroke="var(--brand-blue-soft)" stroke-width="1.3"/><path d="M5 8V2h6v6" fill="none" stroke="var(--brand-blue-soft)" stroke-width="1.3"/></svg>
        555.014.7731
      </p>
      <p class="contact__line contact__line--email">
        <svg class="icon" viewBox="0 0 16 16"><rect x="1" y="3.5" width="14" height="9" fill="var(--brand-blue)"/><path d="M1 3.5l7 5 7-5" fill="none" stroke="var(--paper)" stroke-width="1.2"/></svg>
        dana@brightlanepa.org
      </p>
      <p class="contact__line contact__line--web">
        <svg class="icon" viewBox="0 0 16 16"><circle cx="8" cy="8" r="6" fill="none" stroke="var(--brand-blue)" stroke-width="1.3"/><path d="M2 8h12M8 2c-3 3.5-3 8.5 0 12M8 2c3 3.5 3 8.5 0 12" fill="none" stroke="var(--brand-blue)" stroke-width="1"/></svg>
        www.brightlanepa.org
      </p>
    </div>
    <div class="brand brand--footer">
      <span class="brand__dot"></span>
      <p class="brand__name">Brightlane Associates LLC</p>
      <p class="brand__tagline">Supporting schools &amp; school leaders</p>
    </div>
  </section>

  <section class="panel panel--blue panel--statement">
    <div class="backdrop-disc"></div>
    <div class="headline">
      <p class="headline__lead">School leadership is</p>
      <p class="headline__figure">24/7/365</p>
    </div>
  </section>

  <section class="panel panel--light panel--cover">
    <div class="brand brand--masthead">
      <span class="brand__dot"></span>
      <p class="brand__name">Brightlane Associates LLC</p>
      <p class="brand__tagline">Supporting schools &amp; school leaders</p>
    </div>
    <div class="photo photo--children" role="img" aria-label="Photo of cheerful schoolchildren with backpacks raising their arms"></div>
    <p class="pitch">Let’s work together to take your school to the next level of excellence.</p>
    <div class="callout">
      <p class="callout__phone">
        <svg class="icon" viewBox="0 0 16 16"><circle cx="8" cy="8" r="7" fill="none" stroke="var(--brand-blue-soft)" stroke-width="1.3"/><path d="M5.5 4.5c-.8 2.5.8 6 4 7l1-1.5-1.6-1-1 .8c-.8-.6-1.5-1.6-1.7-2.6l1-.6-.6-1.8z" fill="var(--brand-blue-soft)"/></svg>
        555.014.2290
      </p>
      <p class="callout__web">
        <svg class="icon" viewBox="0 0 16 16"><circle cx="8" cy="8" r="6" fill="none" stroke="var(--brand-blue-soft)" stroke-width="1.3"/><path d="M2 8h12M8 2c-3 3.5-3 8.5 0 12M8 2c3 3.5 3 8.5 0 12" fill="none" stroke="var(--brand-blue-soft)" stroke-width="1"/></svg>
        www.brightlanepa.org
      </p>
    </div>
  </section>

</main>
</body>
</html>
```